Local massage therapist needs some new marketing material

Hi there! I am a massage therapist here in Denver, CO in Alder Bend(shopping and art district) of the city. My business is called Lumo Bodywork of Denver. My practice has an eastern influence and I do reflexology, thai massage and use Chinese herbs, etc. I know all my clients and pay close attention to details. I am also very respectful of tradition and it shows in how I work. I tend to like modern, clean, fun, Asian designs. I am wanting a new business card and brochure. I have a logo and branding for my business that I want used in the design. Currently, the sign for my building is purple and I think my logo was designed to be purple. I will attach pictures of it and can send whatever files are necessary so it can be integrated into the brochure, etc. I like the purple but open to using other colors as well. Thanks!
My website is lumobodyworkofdenver.example where info can be gathered about me and services/fees for brochure.
Updates

Just increased budget. Please see new feedback in discussion thread.

Thanks!

                                       HEY ALL,

Just wanted to let you know that I made a change to my website. It is on the Prices Page. I no longer have the frequent  flyer prices but I added discounts. Let me know if you have any questions. Thanks so much!

Target Market(s)

healthy, urban, educated, upper middle class, yogis

Industry/Entity Type

Marketing

Requirements
Must have
• logo stays purple
Should not have
• not too busy

```html
<!DOCTYPE html>
<html lang="en">
<head>
<meta charset="utf-8">
<title>Lumo Bodywork of Denver – Business Card</title>
<link rel="stylesheet" href="https://fonts.googleapis.com/css2?family=Source+Sans+3:ital,wght@0,400;0,600;0,700;1,400&display=swap">
<style>
  :root{
    --purple:#5b2d8e;
    --purple-band:#5f2f93;
    --ink:#3a3a3a;
    --muted:#6d6d6d;
    --rule:#8a8a8a;
    --paper:#ffffff;
    --backdrop:#ecebe8;
  }
  *{box-sizing:border-box;margin:0;padding:0}
  html,body{width:1200px;height:720px;overflow:hidden}
  body{
    background:var(--backdrop);
    font-family:"Source Sans 3",Arial,sans-serif;
    color:var(--ink);
    position:relative;
  }
  .card{
    position:absolute;
    width:520px;height:297px;
    background:var(--paper);
    box-shadow:0 2px 10px rgba(0,0,0,.12);
    overflow:hidden;
  }
  /* ---------- front ---------- */
  .card--front{left:45px;top:212px}
  .brand{
    position:absolute;left:30px;top:42px;width:200px;
    display:flex;flex-direction:column;align-items:center;gap:16px;
  }
  .brand__dot{width:76px;height:76px;border-radius:50%;background:var(--purple)}
  .brand__name{
    font-weight:400;font-size:52px;letter-spacing:9px;color:var(--purple);line-height:1;
    padding-left:9px;
  }
  .divider{position:absolute;left:252px;top:40px;width:1px;height:110px;background:var(--rule)}
  .contact{position:absolute;left:270px;top:36px}
  .contact__name{font-weight:700;font-size:19px;color:var(--purple);line-height:1.1}
  .contact__title{font-size:12px;color:var(--ink);margin:2px 0 10px}
  .contact__row{display:flex;align-items:center;gap:7px;font-size:13px;line-height:1.55}
  .contact__row svg{width:12px;height:12px;flex:none}
  .band-rule{position:absolute;left:0;right:0;top:236px;height:2px;background:#222}
  .address-band{
    position:absolute;left:0;right:0;top:242px;height:36px;
    background:var(--purple-band);color:#fff;
    font-size:14px;letter-spacing:.3px;
    display:flex;align-items:center;padding-left:270px;
  }
  /* ---------- back ---------- */
  .card--back{left:635px;top:212px}
  .back-brand{position:absolute;right:26px;top:24px;display:flex;align-items:center;gap:8px}
  .back-brand__dot{width:24px;height:24px;border-radius:50%;background:var(--purple)}
  .back-brand__name{font-size:32px;letter-spacing:5px;color:var(--purple);line-height:1}
  .appt{position:absolute;left:34px;top:88px;right:34px}
  .appt__heading{
    font-weight:700;font-size:15px;color:var(--purple);letter-spacing:.3px;
    padding-bottom:6px;border-bottom:1px solid var(--rule);width:420px;
  }
  .field-row{display:flex;align-items:flex-end;gap:6px;font-size:15px;margin-top:20px}
  .field-line{display:inline-block;border-bottom:1px solid var(--rule);height:1px}
  .hours{margin-top:18px;font-size:15.5px;line-height:1.3;color:var(--ink)}
  .note{margin-top:10px;font-style:italic;font-size:15px;color:var(--muted)}
</style>
</head>
<body>

<section class="card card--front" aria-label="Business card front">
  <div class="brand">
    <span class="brand__dot" aria-hidden="true"></span>
    <span class="brand__name">LUMO</span>
  </div>
  <div class="divider"></div>
  <div class="contact">
    <p class="contact__name">Your Name</p>
    <p class="contact__title">Title</p>
    <p class="contact__row">
      <svg viewBox="0 0 12 12" aria-hidden="true"><circle cx="6" cy="6" r="5.4" fill="none" stroke="#5b2d8e" stroke-width="1.2"/><path d="M4 3.2l1 1-.6.9a4 4 0 0 0 1.5 1.5l.9-.6 1 1-.7.9c-2 0-3.9-1.9-3.9-3.9z" fill="#5b2d8e"/></svg>
      303.555.0148
    </p>
    <p class="contact__row">
      <svg viewBox="0 0 12 12" aria-hidden="true"><circle cx="6" cy="6" r="6" fill="#5b2d8e"/><rect x="3" y="4" width="6" height="4.2" fill="#fff"/><path d="M3 4l3 2.3L9 4" fill="none" stroke="#5b2d8e" stroke-width=".8"/></svg>
      info@lumobodyworkofdenver.example
    </p>
    <p class="contact__row">
      <svg viewBox="0 0 12 12" aria-hidden="true"><circle cx="6" cy="6" r="6" fill="#5b2d8e"/><circle cx="6" cy="6" r="3.3" fill="none" stroke="#fff" stroke-width=".8"/><path d="M2.7 6h6.6M6 2.7c-1.5 1.8-1.5 4.8 0 6.6M6 2.7c1.5 1.8 1.5 4.8 0 6.6" fill="none" stroke="#fff" stroke-width=".7"/></svg>
      www.lumobodyworkofdenver.example
    </p>
  </div>
  <div class="band-rule"></div>
  <div class="address-band">1480 E Alder Ln, Denver, CO 80206</div>
</section>

<section class="card card--back" aria-label="Appointment card back">
  <div class="back-brand">
    <span class="back-brand__dot" aria-hidden="true"></span>
    <span class="back-brand__name">LUMO</span>
  </div>
  <div class="appt">
    <h2 class="appt__heading">YOUR APPOINTMENT</h2>
    <div class="field-row">
      <span>Name :</span><span class="field-line" style="width:120px"></span>
      <span>Time :</span><span class="field-line" style="width:110px"></span>
      <span>am / pm</span>
    </div>
    <div class="field-row">
      <span>Date :</span><span class="field-line" style="width:110px"></span>
    </div>
    <p class="hours">Tues - Fri 10am - 8pm Sat 10am-5pm<br>(Appointments required) No walk-ins please.</p>
    <p class="note">We appreciate a 24 hr. notice for cancellations</p>
  </div>
</section>

</body>
</html>
```